Ward Compass Business Card Design*

We need a business card design for our company Ward Compass. Our company is specialized in providing online consulting services regarding medical institutions, hospitals and doctors. We work with patients worldwide looking to choose between healthcare providers. We have a website you may use as a reference, where we list doctors and clinics worldwide. So we target Medical providers as well as patients worldwide.
Target Market(s)
Medical Providers and patients around the world
Industry/Entity Type
Medical
Contact Information for Business Card
Salwa Kettani
CEO
+90 612 348 2175
info@wardcompass.example
www.wardcompass.example
14 Annakhil 7 H.R.B. Rabat, Morocco
Requirements
Must have
- Company logo/name on one full side, personal info and smaller logo and company name on the other side.
Nice to have
- Smart and elegant design

```html
<!DOCTYPE html>
<html lang="en">
<head>
<meta charset="utf-8">
<title>Ward Compass – Business Cards</title>
<link rel="stylesheet" href="https://fonts.googleapis.com/css2?family=Montserrat:wght@300;400;600;700;800&display=swap">
<style>
  :root {
    --navy: #173a6b;
    --grey: #8a8a8a;
    --ink: #2b2b2b;
    --paper: #ffffff;
    --backdrop: #e9e9ea;
  }
  * { box-sizing: border-box; margin: 0; padding: 0; }
  html, body {
    width: 1200px; height: 900px; overflow: hidden;
    background: var(--backdrop);
    font-family: "Montserrat", sans-serif;
  }
  .canvas {
    position: relative; width: 1200px; height: 900px;
  }
  .card {
    position: absolute; left: 260px; width: 680px; height: 388px;
    background: var(--paper);
    box-shadow: 0 2px 10px rgba(0,0,0,0.08);
  }
  .card--front { top: 45px; }
  .card--back { top: 473px; }

  .brand {
    display: flex; align-items: center; gap: 14px;
    color: var(--navy); font-weight: 700; text-transform: uppercase;
    white-space: nowrap;
  }
  .brand__dot {
    border-radius: 50%; background: var(--navy); flex: none;
  }

  /* Front */
  .front__brand {
    position: absolute; left: 0; right: 0; top: 140px;
    justify-content: center; font-size: 40px; letter-spacing: 1px;
  }
  .front__brand .brand__dot { width: 46px; height: 46px; }
  .front__url {
    position: absolute; left: 0; right: 0; top: 268px;
    text-align: center; font-size: 15px; font-weight: 400;
    letter-spacing: 7px; color: var(--ink);
  }

  /* Back */
  .back__brand {
    position: absolute; left: 150px; top: 62px;
    font-size: 30px; letter-spacing: 1px;
  }
  .back__brand .brand__dot { width: 36px; height: 36px; }
  .person {
    position: absolute; right: 372px; top: 150px; text-align: right;
  }
  .person__name {
    font-size: 30px; font-weight: 800; line-height: 1.1; white-space: nowrap;
  }
  .person__first { color: var(--navy); }
  .person__last { color: var(--grey); }
  .person__role {
    font-size: 18px; font-weight: 300; color: var(--navy); letter-spacing: 1px;
  }
  .divider {
    position: absolute; left: 330px; top: 140px; width: 2px; height: 86px;
    background: var(--navy);
  }
  .contacts {
    position: absolute; left: 352px; top: 140px;
    list-style: none; display: flex; flex-direction: column; gap: 8px;
  }
  .contacts__item {
    display: flex; align-items: center; gap: 10px;
    font-size: 15px; color: var(--ink); font-weight: 400;
  }
  .contacts__icon { width: 17px; height: 17px; flex: none; }
  .address {
    position: absolute; left: 0; right: 0; top: 300px;
    text-align: center; font-size: 19px; color: var(--ink); font-weight: 400;
  }
</style>
</head>
<body>
<main class="canvas">
  <section class="card card--front" aria-label="Business card front">
    <div class="brand front__brand">
      <span class="brand__dot"></span>
      <span class="brand__name">Ward Compass</span>
    </div>
    <p class="front__url">www.wardcompass.example</p>
  </section>

  <section class="card card--back" aria-label="Business card back">
    <div class="brand back__brand">
      <span class="brand__dot"></span>
      <span class="brand__name">Ward Compass</span>
    </div>

    <div class="person">
      <p class="person__name"><span class="person__first">Salwa</span> <span class="person__last">Kettani</span></p>
      <p class="person__role">CEO</p>
    </div>

    <span class="divider"></span>

    <ul class="contacts">
      <li class="contacts__item">
        <svg class="contacts__icon" viewBox="0 0 24 24" aria-hidden="true">
          <path fill="#173a6b" d="M6.6 10.8c1.4 2.8 3.8 5.1 6.6 6.6l2.2-2.2c.3-.3.7-.4 1-.2 1.1.4 2.3.6 3.6.6.6 0 1 .4 1 1V20c0 .6-.4 1-1 1C10.6 21 3 13.4 3 4c0-.6.4-1 1-1h3.5c.6 0 1 .4 1 1 0 1.3.2 2.5.6 3.6.1.3 0 .7-.2 1z"/>
        </svg>
        <span>+90 612 348 2175</span>
      </li>
      <li class="contacts__item">
        <svg class="contacts__icon" viewBox="0 0 24 24" aria-hidden="true">
          <rect x="2" y="5" width="20" height="14" rx="1" fill="#173a6b"/>
          <path d="M3 6l9 7 9-7" fill="none" stroke="#fff" stroke-width="1.6"/>
        </svg>
        <span>info@wardcompass.example</span>
      </li>
      <li class="contacts__item">
        <svg class="contacts__icon" viewBox="0 0 24 24" aria-hidden="true">
          <circle cx="12" cy="12" r="10" fill="#173a6b"/>
          <g fill="none" stroke="#fff" stroke-width="1.2">
            <ellipse cx="12" cy="12" rx="4" ry="9"/>
            <path d="M3 12h18M5 7h14M5 17h14"/>
          </g>
        </svg>
        <span>www.wardcompass.example</span>
      </li>
    </ul>

    <p class="address">14 Annakhil 7 H.R.B. Rabat, Morocco</p>
  </section>
</main>
</body>
</html>
```